Dashboard Elements

Hello – looking for someone to create dashboard elements.
I’ve already basically designed all these elements – but I need someone to take what I’ve designed and make it look like an actual dashboard UI, like an app - assuming using some kind of dashboard UI kit (but however you would like to get it done is fine). It can look just like mine or try something different, as long as it matches the color scheme webpage that I’m going to out it on – see the page here. I’m ok with making it dark, maybe that would look better – again as long as it matches the webpage (https://www.plandeck.io/file/7QxKtr2BwLpZnVe4Hs8Mc1/Webpage-with-placeholders?node-id=0%3A1). Please note, you do not need to put anything on the webpage or do anything with this Figma file, this is just a reference so you can color/stylize it accordingly.

The attached Powerpoint file has everything you need - make sure to zoom all the way out to see everything on the slides.

Here are the Dashboard elements needed (this will all make sense when you look at the PPT):
Dashboard 1
Dashboard 1 – expanded view A
Dashboard 1 – expanded view B
View Source button by itself
Source Document Viewer 1 and 2 (these are exactly the same just with a different image inside)*
Dashboard 2 (only slightly different than Dashboard 1, just extended with extra headings
Table of Contents
Searchbar and Source Doc by itself
*the documents in the source document viewers should still look like documents - they don’t need to look like part of the UI, because this is a document viewer – you can restyle/recolor if necessary or just leave these as is.
- Colors must match color scheme of webpage, attached and on Figma link (images there currently are only placeholders) – ok to go dark as long as it matches
- Must look sleek, clean, realistic
- Don’t add any pictures of people or change the text.
- In case it’s not clear, this is what I mean by the concept of Dashboard UI - https://www.notavia.net/shard/s7/sh/8fad21bc-14e9-4a7c-b2d0-5c3e9f71a604/92c4e1b7a05d3f68e1c2b947d0a3f815
- Must be sent in an editable file, I may need to be edit text and other elements
- If you are going to send a sample, please make sure it’s part of the dashboard itself, not just the table of contents etc

Ideally hoping to find someone I can continue working with as I'll have a lot more graphic design work needed coming up.

Thank you!

```html
<!DOCTYPE html>
<html lang="en">
<head>
<meta charset="utf-8">
<title>Summarized and Linked to Key Insights</title>
<link href="https://fonts.googleapis.com/css2?family=Exo+2:wght@300&family=Roboto:wght@300;400;500;700&display=swap" rel="stylesheet">
<style>
:root{
  --page-bg:#14131f;
  --ink:#ffffff;
  --ink-soft:#b7bccb;
  --violet-panel:#2c336c;
  --violet-panel-2:#283062;
  --violet-frame:rgba(130,150,230,.35);
  --violet-card-a:#4a4590;
  --violet-card-b:#7c70c2;
  --violet-tab:#2a2f58;
  --code-blue:#5aa2d8;
  --teal:#2fb8aa;
  --teal-bright:#45d4c4;
  --teal-card-a:#17897f;
  --teal-card-b:#36c2b2;
  --btn-a:#1f9e92;
  --btn-b:#3ccab9;
  --ornament-a:#7a6fd0;
  --ornament-b:#3ec6b8;
}
*{box-sizing:border-box;margin:0;padding:0}
html,body{width:1200px;height:3599px;overflow:hidden}
body{
  position:relative;
  background:
    radial-gradient(ellipse 260px 420px at 1180px 380px,rgba(40,150,150,.35),transparent 70%),
    radial-gradient(ellipse 320px 300px at 80px 420px,rgba(40,140,130,.30),transparent 70%),
    radial-gradient(ellipse 300px 360px at 40px 1350px,rgba(40,150,140,.22),transparent 70%),
    radial-gradient(ellipse 300px 400px at 1180px 1500px,rgba(40,140,150,.22),transparent 70%),
    radial-gradient(ellipse 280px 380px at 60px 2350px,rgba(40,150,140,.20),transparent 70%),
    radial-gradient(ellipse 300px 400px at 1170px 2700px,rgba(40,140,150,.20),transparent 70%),
    radial-gradient(ellipse 300px 300px at 100px 3300px,rgba(40,150,140,.18),transparent 70%),
    var(--page-bg);
  font-family:"Roboto",Arial,sans-serif;color:var(--ink);
}
.top-rule{position:absolute;left:591px;top:0;width:1px;height:21px;background:rgba(255,255,255,.25)}
.intro{
  position:absolute;left:84px;top:21px;width:1034px;height:583px;border-radius:14px;
  background:linear-gradient(180deg,rgba(255,255,255,.05),rgba(255,255,255,.015));
  border:1px solid rgba(255,255,255,.05);
}
.intro-title{
  position:absolute;left:0;top:86px;width:100%;text-align:center;
  font-family:"Exo 2",Arial,sans-serif;font-weight:300;font-size:40px;line-height:50px;letter-spacing:4px;color:#e6e8ee;
}
.intro-text{
  position:absolute;left:0;top:200px;width:100%;text-align:center;
  font-size:16px;line-height:27px;font-weight:300;color:var(--ink-soft);
}
.section-title{position:absolute;left:0;width:1200px;text-align:center;font-weight:500;font-size:28px;line-height:34px}

.panel{position:absolute;left:327px;width:535px;font-size:10px}
.panel--violet{background:linear-gradient(180deg,var(--violet-panel),var(--violet-panel-2));box-shadow:0 10px 24px rgba(0,0,0,.4)}
.panel--violet::before{content:"";position:absolute;left:19px;right:12px;top:15px;bottom:12px;border:1px solid var(--violet-frame);border-radius:3px}
.corner-ornament{position:absolute;left:0;top:0;width:24px;height:24px;background:linear-gradient(135deg,var(--ornament-a),var(--ornament-b))}
.panel--teal{background:rgba(18,30,44,.92);border:2px solid var(--teal);box-shadow:0 0 16px rgba(47,184,170,.55),inset 0 0 14px rgba(47,184,170,.2)}
.teal-frame{position:absolute;left:0;top:0;width:100%;height:100%}
.beam{position:absolute;left:540px;width:120px;height:54px;background:linear-gradient(180deg,rgba(47,184,170,.15),transparent);clip-path:polygon(0 0,100% 0,56% 100%,44% 100%)}
.beam-dot{position:absolute;left:588px;width:24px;height:6px;border-radius:50%;background:var(--teal-bright);box-shadow:0 0 10px 3px rgba(69,212,196,.7)}

.brand{position:absolute;left:43px;top:38px;display:flex;align-items:center;gap:6px;font-size:14px;font-weight:400;letter-spacing:.3px}
.brand-dot{width:12px;height:12px;border-radius:50%;background:#c9d3f5}
.tab{position:absolute;left:193px;top:24px;width:150px;height:28px;display:flex;align-items:center;justify-content:center;font-size:13px;font-weight:500;background:var(--violet-tab);box-shadow:0 3px 6px rgba(0,0,0,.45)}
.panel--teal .tab{background:none;box-shadow:none;color:var(--teal-bright);font-size:14px}
.patient{position:absolute;right:32px;top:38px;text-align:right;font-size:10px;line-height:18px;font-weight:500}
.patient svg{vertical-align:-2px;margin-right:3px}
.panel--teal .patient{color:var(--teal-bright)}
.hcc-toggle{position:absolute;left:34px;top:98px;font-size:10px;font-weight:500;display:flex;align-items:center;gap:8px}
.tri-down{width:0;height:0;border-left:7px solid transparent;border-right:7px solid transparent;border-top:8px solid #fff}
.panel--teal .tri-down{border-top-color:var(--teal-bright)}
.panel--teal .hcc-toggle{color:var(--teal-bright)}
.raf-badge{position:absolute;left:272px;top:92px;width:243px;height:24px;display:flex;align-items:center;justify-content:center;font-size:9.5px;font-weight:500;background:linear-gradient(90deg,var(--btn-a),var(--btn-b))}
.raf-badge .muted{opacity:.65;margin-right:3px}
.panel--teal .raf-badge{background:none;border:1px solid var(--teal);color:var(--teal-bright)}
.hcc-head{position:absolute;left:21px;top:134px;width:493px;height:48px;background:linear-gradient(90deg,#5a5aa8,#7b72c0);box-shadow:0 4px 10px rgba(0,0,0,.4)}
.panel--teal .hcc-head{background:none;border:1.5px solid var(--teal);box-shadow:0 0 8px rgba(47,184,170,.4)}
.hcc-head span,.hcc-row span{position:absolute;top:50%;transform:translateY(-50%);white-space:nowrap}
.hcc-row{position:absolute;left:0;width:100%;height:30px;margin-top:-15px}
.hcc-row::after{content:"";position:absolute;left:21px;width:493px;bottom:-8px;height:1px;background:rgba(130,150,230,.3)}
.panel--teal .hcc-row::after{background:rgba(47,184,170,.3)}
.hcc-row--bare::after{display:none}
.col-code{left:35px}.col-cond{left:123px}.col-cat{left:359px}.col-raf{left:425px}
.hcc-row .col-code,.hcc-row .col-raf{color:var(--code-blue)}
.hcc-row .col-cond{font-weight:500}
.panel--teal .hcc-row .col-code,.panel--teal .hcc-row .col-raf{color:#7fa8b8}
.panel--teal .hcc-row .col-cond{color:var(--teal-bright)}
.chev{position:absolute;left:470px;top:11px;width:0;height:0;border-left:7px solid transparent;border-right:7px solid transparent;border-top:8px solid #fff}
.chev--up{border-top:0;border-bottom:8px solid #fff}
.panel--teal .chev{border-top-color:var(--teal-bright)}
.panel--teal .chev--up{border-bottom-color:var(--teal-bright)}
.why{position:absolute;left:35px;font-size:9.5px;color:#dfe3f3;white-space:nowrap}
.why b{font-weight:700}
.panel--teal .why{color:var(--teal-bright)}

.line-item{position:absolute;left:35px;font-size:10px;color:#dfe3f3;white-space:nowrap}
.panel--teal .line-item{color:var(--teal-bright)}
.src-tag{position:absolute;left:193px;width:150px;height:26px;display:flex;align-items:center;justify-content:center;font-size:10px;font-weight:500;background:var(--violet-tab);box-shadow:0 3px 6px rgba(0,0,0,.45)}
.panel--teal .src-tag{background:none;border:1.5px solid var(--teal);box-shadow:none}
.btn-source{position:absolute;width:113px;height:25px;display:flex;align-items:center;justify-content:center;gap:9px;font-size:10px;font-weight:500;color:#fff;background:linear-gradient(90deg,var(--btn-a),var(--btn-b));box-shadow:0 3px 7px rgba(0,0,0,.45)}
.btn-source--violet{background:linear-gradient(90deg,#4f4a98,#6f66b8);color:#7fe0d4}
.btn-source svg{flex:none}
.card{position:absolute;background:linear-gradient(90deg,var(--violet-card-a),var(--violet-card-b));box-shadow:0 6px 14px rgba(0,0,0,.5);font-size:10px}
.card--teal{background:linear-gradient(90deg,var(--teal-card-a),var(--teal-card-b));box-shadow:0 0 12px rgba(47,184,170,.45)}
.card-label{position:absolute;top:50%;transform:translateY(-50%);font-weight:500}
.card-info{position:absolute;top:50%;transform:translateY(-50%);line-height:11px;font-size:9.5px;white-space:nowrap}
.card-info b{font-weight:700}
.history{position:absolute;left:0;width:100%;font-size:9.5px;line-height:11.5px}
.history-title{text-align:center;font-weight:500}
.history-grid{position:absolute;left:184px;top:16px;display:grid;grid-template-columns:111px auto}
.panel--teal .history{color:var(--teal-bright)}
.float-btn{position:absolute}
</style>
</head>
<body>
<svg width="0" height="0" style="position:absolute">
  <defs>
    <symbol id="icon-db" viewBox="0 0 20 20">
      <ellipse cx="8" cy="4" rx="7" ry="2.5" fill="#fff"/>
      <path d="M1 6.5c0 1.4 3.1 2.5 7 2.5s7-1.1 7-2.5v3c0 1.4-3.1 2.5-7 2.5s-7-1.1-7-2.5z" fill="#fff"/>
      <path d="M1 11.5c0 1.4 3.1 2.5 7 2.5l1 0v3l-1 0c-3.9 0-7-1.1-7-2.5z" fill="#fff"/>
      <circle cx="14" cy="14" r="3.2" fill="none" stroke="#fff" stroke-width="1.8"/>
      <path d="M16.3 16.3l2.6 2.6" stroke="#fff" stroke-width="2" stroke-linecap="round"/>
    </symbol>
    <symbol id="icon-user" viewBox="0 0 10 10">
      <circle cx="5" cy="3" r="2.4" fill="currentColor"/>
      <path d="M0.5 10c0-2.8 2-4.3 4.5-4.3s4.5 1.5 4.5 4.3z" fill="currentColor"/>
    </symbol>
  </defs>
</svg>

<div class="top-rule"></div>
<section class="intro">
  <h1 class="intro-title">SUMMARIZED AND LINKED<br>TO KEY INSIGHTS</h1>
  <p class="intro-text">Insights are presented in a concise summary with direct links to supporting evidence.<br>HCC opportunities are abstracted and cross-linked directly to the original text in the<br>underlying record for quick and easy reference.</p>
</section>

<!-- Violet: Dashboard 1 -->
<h2 class="section-title" style="top:458px">Dashboard 1</h2>
<div class="panel panel--violet" style="top:508px;height:427px">
  <div class="corner-ornament" role="img" aria-label="Decorative pixel-square corner ornament"></div>
  <div class="brand"><span class="brand-dot"></span>NOVACHART</div>
  <div class="tab">C-CDA Compendium</div>
  <div class="patient"><svg width="10" height="10"><use href="#icon-user"/></svg>Patient, Mary<br><svg width="10" height="10"><use href="#icon-user"/></svg>Female | 01/11/1951 | Age: 70</div>
  <div class="hcc-toggle"><span class="tri-down"></span>HCC Summary</div>
  <div class="raf-badge"><span class="muted">RAF: 2.362 |</span> Condition Count: 8 | ID: 7326472</div>
  <div class="hcc-head"><span style="left:14px">ICD-10 Code</span><span style="left:102px">Condition</span><span style="left:338px">Category</span><span style="left:404px">RAF</span></div>
  <div class="hcc-row" style="top:210px"><span class="col-code">J44.9</span><span class="col-cond">Chronic obstructive pulmonary disease</span><span class="col-cat">111</span><span class="col-raf">0.335</span><i class="chev"></i></div>
  <div class="hcc-row" style="top:259px"><span class="col-code">F33.1</span><span class="col-cond">Chronic kidney disease, moderate (stage 3)</span><span class="col-cat">138</span><span class="col-raf">0.069</span><i class="chev"></i></div>
  <div class="hcc-row" style="top:301px"><span class="col-code">F33.0</span><span class="col-cond">Major depressive disorder, recurrent, mild</span><span class="col-cat">59</span><span class="col-raf">0.309</span><i class="chev"></i></div>
  <div class="hcc-row" style="top:343px"><span class="col-code">I42.9</span><span class="col-cond">Cardiomyopathy</span><span class="col-cat">85</span><span class="col-raf">0.447</span><i class="chev"></i></div>
  <div class="hcc-row" style="top:386px"><span class="col-code">E11.36</span><span class="col-cond">Type 2 diabetes mellitus with diabetic cataract</span><span class="col-cat">18</span><span class="col-raf">0.302</span><i class="chev"></i></div>
</div>

<!-- Violet: Expanded view A -->
<h2 class="section-title" style="top:971px">Dashboard 1 – Expanded view A</h2>
<div class="panel panel--violet" style="top:1014px;height:428px">
  <div class="corner-ornament" role="img" aria-label="Decorative pixel-square corner ornament"></div>
  <div class="hcc-row hcc-row--bare" style="top:49px"><span class="col-code">E11.36</span><span class="col-cond">Type 2 diabetes mellitus with diabetic cataract</span><span class="col-cat">18</span><span class="col-raf">0.302</span><i class="chev chev--up"></i></div>
  <p class="why" style="top:65px"><b>Why:</b> This patient was treated for cataracts that may be associated with type 2 diabetes mellitus</p>
  <p class="line-item" style="top:124px">Extracapsular Cataract With IOL</p>
  <div class="src-tag" style="top:118px">C-CDA: Procedures</div>
  <div class="btn-source btn-source--violet" style="left:388px;top:118px"><svg width="18" height="18"><use href="#icon-db"/></svg>View Source</div>
  <div class="card" style="left:-67px;top:162px;width:469px;height:64px">
    <span class="card-label" style="left:32px">Cataract</span>
    <span class="card-info" style="left:150px"><b>Ophthalmology Chart Note</b><br>Patient presents for cataract<br>evaluation in the right eye.</span>
    <div class="btn-source" style="left:336px;top:20px"><svg width="18" height="18"><use href="#icon-db"/></svg>View Source</div>
  </div>
  <p class="line-item" style="top:252px">Diabetes Type 2</p>
  <div class="src-tag" style="top:245px">C-CDA: Problem List</div>
  <div class="btn-source btn-source--violet" style="left:388px;top:245px"><svg width="18" height="18"><use href="#icon-db"/></svg>View Source</div>
  <div class="card" style="left:140px;top:300px;width:468px;height:67px">
    <span class="card-label" style="left:32px">HbA1c</span>
    <span class="card-info" style="left:173px"><b>Lab Results</b><br>Hemoglobin A1C<br>6.9%<br>01/15/21</span>
    <div class="btn-source" style="left:333px;top:21px"><svg width="18" height="18"><use href="#icon-db"/></svg>View Source</div>
  </div>
</div>

<!-- Violet: Expanded view B -->
<h2 class="section-title" style="top:1485px">Dashboard 1 – Expanded view B</h2>
<div class="panel panel--violet" style="top:1528px;height:322px">
  <div class="corner-ornament" role="img" aria-label="Decorative pixel-square corner ornament"></div>
  <div class="hcc-row hcc-row--bare" style="top:49px"><span class="col-code">N18.31</span><span class="col-cond">Chronic kidney disease, stage 3a</span><span class="col-cat">138</span><span class="col-raf">0.069</span><i class="chev chev--up"></i></div>
  <p class="why" style="top:67px"><b>Why:</b> This patient has an eGFR bewtween 45-59 mL/min</p>
  <div class="card" style="left:34px;top:116px;width:471px;height:66px">
    <span class="card-label" style="left:30px">eGFR</span>
    <span class="card-info" style="left:198px;text-align:center"><b>Lab Results</b><br>47mL/min<br>05/26/2021</span>
    <div class="btn-source" style="left:334px;top:21px"><svg width="18" height="18"><use href="#icon-db"/></svg>View Source</div>
  </div>
  <div class="history" style="top:221px">
    <p class="history-title">History</p>
    <div class="history-grid"><span>45mL/min</span><span>03/17/21</span><span>41mL/min</span><span>01/14/21</span><span>52mL/min</span><span>10/15/20</span><span>44mL/min</span><span>06/22/20</span></div>
  </div>
</div>
<div class="btn-source float-btn" style="left:881px;top:1743px"><svg width="18" height="18"><use href="#icon-db"/></svg>View Source</div>

<!-- Teal: Dashboard 1 -->
<h2 class="section-title" style="top:1883px">Dashboard 1</h2>
<div class="panel panel--teal" style="top:1929px;height:429px">
  <svg class="teal-frame" viewBox="0 0 535 429" preserveAspectRatio="none"><polyline points="34,12 501,12 521,32 521,397 501,417 34,417 14,397 14,32 34,12" fill="none" stroke="#2fb8aa" stroke-opacity=".55" stroke-width="1.5"/></svg>
  <div class="brand"><span class="brand-dot"></span>NOVACHART</div>
  <div class="tab" style="top:30px">C-CDA Compendium</div>
  <div class="patient"><svg width="10" height="10"><use href="#icon-user"/></svg>Patient, Mary<br><svg width="10" height="10"><use href="#icon-user"/></svg>Female | 01/11/1951 | Age: 70</div>
  <div class="hcc-toggle"><span class="tri-down"></span>HCC Summary</div>
  <div class="raf-badge"><span class="muted">RAF: 2.362 |</span> Condition Count: 8 | ID: 7326472</div>
  <div class="hcc-head"><span style="left:14px">ICD-10 Code</span><span style="left:102px">Condition</span><span style="left:338px">Category</span><span style="left:404px">RAF</span></div>
  <div class="hcc-row" style="top:210px"><span class="col-code">J44.9</span><span class="col-cond">Chronic obstructive pulmonary disease</span><span class="col-cat">111</span><span class="col-raf">0.335</span><i class="chev"></i></div>
  <div class="hcc-row" style="top:256px"><span class="col-code">F33.1</span><span class="col-cond">Chronic kidney disease, moderate (stage 3)</span><span class="col-cat">138</span><span class="col-raf">0.069</span><i class="chev"></i></div>
  <div class="hcc-row" style="top:297px"><span class="col-code">F33.0</span><span class="col-cond">Major depressive disorder, recurrent, mild</span><span class="col-cat">59</span><span class="col-raf">0.309</span><i class="chev"></i></div>
  <div class="hcc-row" style="top:336px"><span class="col-code">I42.9</span><span class="col-cond">Cardiomyopathy</span><span class="col-cat">85</span><span class="col-raf">0.447</span><i class="chev"></i></div>
  <div class="hcc-row hcc-row--bare" style="top:376px"><span class="col-code">E11.36</span><span class="col-cond">Type 2 diabetes mellitus with diabetic cataract</span><span class="col-cat">18</span><span class="col-raf">0.302</span><i class="chev"></i></div>
</div>
<div class="beam" style="top:2358px"></div>
<div class="beam-dot" style="top:2407px"></div>

<!-- Teal: Expanded view A -->
<h2 class="section-title" style="top:2454px">Dashboard 1 – Expanded view A</h2>
<div class="panel panel--teal" style="top:2496px;height:467px">
  <svg class="teal-frame" viewBox="0 0 535 467" preserveAspectRatio="none"><polyline points="34,12 501,12 521,32 521,435 501,455 34,455 14,435 14,32 34,12" fill="none" stroke="#2fb8aa" stroke-opacity=".55" stroke-width="1.5"/></svg>
  <div class="hcc-row hcc-row--bare" style="top:53px"><span class="col-code">E11.36</span><span class="col-cond">Type 2 diabetes mellitus with diabetic cataract</span><span class="col-cat">18</span><span class="col-raf">0.302</span><i class="chev chev--up"></i></div>
  <p class="why" style="top:70px"><b>Why:</b> This patient was treated for cataracts that may be associated with type 2 diabetes mellitus</p>
  <p class="line-item" style="top:134px">Extracapsular Cataract With IOL</p>
  <div class="src-tag" style="top:127px">C-CDA: Procedures</div>
  <div class="btn-source" style="left:388px;top:127px"><svg width="18" height="18"><use href="#icon-db"/></svg>View Source</div>
  <div class="card card--teal" style="left:-117px;top:165px;width:472px;height:67px">
    <span class="card-label" style="left:34px">Cataract</span>
    <span class="card-info" style="left:155px"><b>Ophthalmology Chart Note</b><br>Patient presents for cataract<br>evaluation in the right eye.</span>
    <div class="btn-source" style="left:336px;top:21px"><svg width="18" height="18"><use href="#icon-db"/></svg>View Source</div>
  </div>
  <p class="line-item" style="top:268px">Diabetes Type 2</p>
  <div class="src-tag" style="top:261px">C-CDA: Problem List</div>
  <div class="btn-source" style="left:388px;top:261px"><svg width="18" height="18"><use href="#icon-db"/></svg>View Source</div>
  <div class="card card--teal" style="left:134px;top:303px;width:472px;height:70px">
    <span class="card-label" style="left:40px">HbA1c</span>
    <span class="card-info" style="left:180px"><b>Lab Results</b><br>Hemoglobin A1C<br>6.9%<br>01/15/21</span>
    <div class="btn-source" style="left:336px;top:23px"><svg width="18" height="18"><use href="#icon-db"/></svg>View Source</div>
  </div>
</div>
<div class="beam" style="top:2963px;height:14px"></div>
<div class="beam-dot" style="top:2974px"></div>

<!-- Teal: Expanded view B -->
<h2 class="section-title" style="top:3026px">Dashboard 1 – Expanded view B</h2>
<div class="panel panel--teal" style="top:3069px;height:356px">
  <svg class="teal-frame" viewBox="0 0 535 356" preserveAspectRatio="none"><polyline points="34,12 501,12 521,32 521,324 501,344 34,344 14,324 14,32 34,12" fill="none" stroke="#2fb8aa" stroke-opacity=".55" stroke-width="1.5"/></svg>
  <div class="hcc-row hcc-row--bare" style="top:60px"><span class="col-code">N18.31</span><span class="col-cond">Chronic kidney disease, stage 3a</span><span class="col-cat">138</span><span class="col-raf">0.069</span><i class="chev chev--up"></i></div>
  <p class="why" style="top:77px"><b>Why:</b> This patient has an eGFR bewtween 45-59 mL/min</p>
  <div class="card card--teal" style="left:34px;top:127px;width:471px;height:70px">
    <span class="card-label" style="left:30px">eGFR</span>
    <span class="card-info" style="left:198px;text-align:center"><b>Lab Results</b><br>47mL/min<br>05/26/2021</span>
    <div class="btn-source" style="left:334px;top:23px"><svg width="18" height="18"><use href="#icon-db"/></svg>View Source</div>
  </div>
  <div class="history" style="top:233px">
    <p class="history-title">History</p>
    <div class="history-grid" style="left:192px"><span>45mL/min</span><span>03/17/21</span><span>41mL/min</span><span>01/14/21</span><span>52mL/min</span><span>10/15/20</span><span>44mL/min</span><span>06/22/20</span></div>
  </div>
</div>
<div class="btn-source float-btn" style="left:888px;top:3358px"><svg width="18" height="18"><use href="#icon-db"/></svg>View Source</div>
<div class="beam" style="top:3425px"></div>
<div class="beam-dot" style="top:3474px"></div>
</body>
</html>
```